NZ First of it's kind solutions directory and marketplace for busy Mums needs a business card design

We need a business card design for our new nationwide business in NZ (long term plans to go global). We provide solutions to the everyday challenges that busy Mums face by connecting them with quality communities and suppliers of carefully selected, relevant products and services. We sell direct via our online marketplace. The final design should communicate our values of inclusivity, quality and smart solutions. Colours should incorporate our logo colour palette of #477077 and #6ba8b2. Our website is at https://www.brightnestmums.example

Target Market(s)

busy Mums, Age 28 – 50, female, income over $100K, location main centres NZ primarily but NZ wide. Is likely juggling work or career with a young family. Probably had hobbies which have fallen by the wayside.
-Wants to succeed in her chosen career without compromising on family life
-to successfully juggle her career without feeling like she is compromising her children
- Is time poor, something always has to give and it’s generally her health (she’ll stay up late, get stressed)
- probably ex corporate or professional career. Has discretional income

Industry/Entity Type

Business

Contact Information for Business Card

Lena Forbisher, Founder, BrightNestMums.example (Strapline Tap; Gather; Sorted), 47 Kowhai Terrace, Ellerslie, Auckland 1051, New Zealand. Mob: 021 483 517 Ph: +64 (0)9 571 4860

Font styles to use
Other font styles liked:
• Raleway, and/or Architects Daughter

Colors
00a990
33b8a4
86cfc6
cfeae6

Requirements
Must have
• the above details, streamline. the logo and colours associated with those logos
Should not have
• foil or metallic colours

```html
<!DOCTYPE html>
<html lang="en">
<head>
<meta charset="utf-8">
<title>BrightNestMums – Business Card</title>
<link href="https://fonts.googleapis.com/css2?family=Roboto:wght@400;500;700&family=Roboto+Condensed:wght@700&display=swap" rel="stylesheet">
<style>
  :root {
    --backdrop: #2a2a2a;
    --brand-deep: #477077;
    --brand-light: #6ba8b2;
    --card-paper: #f1f1f1;
    --body-text: #555555;
    --divider: #cfcfcf;
    --white: #ffffff;
  }
  html, body {
    margin: 0;
    padding: 0;
    width: 1200px;
    height: 960px;
    overflow: hidden;
    background: var(--backdrop);
  }
  .stage {
    position: relative;
    width: 1200px;
    height: 960px;
  }
  .card {
    position: absolute;
    width: 600px;
    height: 342px;
    overflow: hidden;
    font-family: "Roboto", Arial, sans-serif;
  }
  .card-front {
    left: 314px;
    top: 113px;
    background: var(--card-paper);
  }
  .card-back {
    left: 311px;
    top: 472px;
    background: var(--brand-light);
  }
  .front-bands {
    position: absolute;
    inset: 0;
  }
  .brand-lockup {
    position: absolute;
    left: 53px;
    top: 150px;
    display: flex;
    align-items: center;
    gap: 10px;
  }
  .brand-dot {
    width: 26px;
    height: 26px;
    border-radius: 50%;
    background: var(--brand-deep);
  }
  .brand-name {
    font-family: "Roboto", Arial, sans-serif;
    font-weight: 700;
    font-size: 30px;
    letter-spacing: -0.5px;
    color: var(--brand-deep);
  }
  .divider {
    position: absolute;
    left: 321px;
    top: 92px;
    width: 1px;
    height: 150px;
    background: var(--divider);
  }
  .contact-block {
    position: absolute;
    left: 349px;
    top: 87px;
    color: var(--body-text);
  }
  .person-name {
    margin: 0;
    font-family: "Roboto Condensed", "Arial Narrow", sans-serif;
    font-weight: 700;
    font-size: 21px;
    color: var(--brand-deep);
    text-transform: uppercase;
    line-height: 1.1;
  }
  .person-role {
    margin: 2px 0 0;
    font-size: 15px;
    font-weight: 500;
    color: var(--brand-light);
    text-transform: uppercase;
    letter-spacing: 0.3px;
  }
  .address {
    margin: 11px 0 10px;
    font-size: 14.5px;
    line-height: 19px;
    font-style: normal;
  }
  .contact-list {
    list-style: none;
    margin: 0;
    padding: 0;
    font-size: 14.5px;
    line-height: 19px;
  }
  .contact-list li {
    display: flex;
    align-items: center;
    gap: 8px;
  }
  .contact-icon {
    width: 14px;
    height: 14px;
    flex: none;
  }
  .back-lockup {
    position: absolute;
    left: 0;
    right: 0;
    top: 140px;
    display: flex;
    justify-content: center;
    align-items: center;
    gap: 14px;
  }
  .back-dot {
    width: 34px;
    height: 34px;
    border-radius: 50%;
    background: var(--white);
  }
  .back-name {
    font-family: "Roboto", Arial, sans-serif;
    font-weight: 700;
    font-size: 40px;
    color: var(--white);
  }
  .strapline {
    position: absolute;
    left: 0;
    right: 0;
    top: 304px;
    margin: 0;
    text-align: center;
    font-size: 15px;
    color: var(--white);
  }
</style>
</head>
<body>
<main class="stage">

  <section class="card card-front" aria-label="Business card front">
    <svg class="front-bands" width="600" height="342" viewBox="0 0 600 342" aria-hidden="true">
      <path d="M0 0 H470 C300 8 90 30 0 68 Z" fill="var(--brand-deep)"/>
      <path d="M600 274 C540 310 300 335 0 342 H600 Z" fill="var(--brand-deep)"/>
    </svg>

    <div class="brand-lockup">
      <span class="brand-dot"></span>
      <span class="brand-name">BrightNestMums</span>
    </div>

    <div class="divider"></div>

    <div class="contact-block">
      <h1 class="person-name">Lena Forbisher</h1>
      <p class="person-role">Founder</p>
      <address class="address">47 Kowhai Terrace, Ellerslie<br>Auckland 1051, New Zealand.</address>
      <ul class="contact-list">
        <li>
          <svg class="contact-icon" viewBox="0 0 14 14" aria-hidden="true"><path d="M3 1 L5 1 L6 4 L4.5 5.5 C5.3 7.3 6.7 8.7 8.5 9.5 L10 8 L13 9 L13 11 C13 12 12 13 11 13 C5.5 13 1 8.5 1 3 C1 2 2 1 3 1 Z" fill="var(--brand-deep)"/></svg>
          <span>+64 (0)9 571 4860</span>
        </li>
        <li>
          <svg class="contact-icon" viewBox="0 0 14 14" aria-hidden="true"><rect x="3" y="0.5" width="8" height="13" rx="1.5" fill="var(--brand-deep)"/><rect x="4.3" y="2" width="5.4" height="8.5" fill="var(--card-paper)"/></svg>
          <span>021 483 517</span>
        </li>
        <li>
          <svg class="contact-icon" viewBox="0 0 14 14" aria-hidden="true"><circle cx="7" cy="7" r="6" fill="var(--brand-deep)"/><path d="M4 4 C6 5 5 7 7 7 C8 8 6 10 8 12 M9 2.5 C9 4 11 4 12 5" stroke="var(--card-paper)" stroke-width="1.2" fill="none"/></svg>
          <span>BrightNestMums.example</span>
        </li>
      </ul>
    </div>
  </section>

  <section class="card card-back" aria-label="Business card back">
    <div class="back-lockup">
      <span class="back-dot"></span>
      <span class="back-name">BrightNestMums</span>
    </div>
    <p class="strapline">Tap; Gather; Sorted</p>
  </section>

</main>
</body>
</html>
```